Venture 482 - Lumora Book Cover

I am looking for a Lumora book cover for my book about "Venture 482".
The Book is Titled:
Venture 482 Ascended
Shaping Outcomes: Paths To Unlocking Cosmic Truths
Author is Dorian Pell
Here is a book description that may help you understand more about it:
Inspired by the genius of Edwin Marlowe, this comprehensive guide delves into the ancient wisdom and cutting-edge science behind the 482 method, a powerful tool for manifesting your desires. Whether you're seeking personal growth, financial success, or spiritual enlightenment, this book provides advanced techniques and methods to transform your dreams into reality.
Any questions please ask.
Thanks
Owen

```html
<!DOCTYPE html>
<html lang="en">
<head>
<meta charset="utf-8">
<title>Venture 482 Ascended — Shaping Outcomes</title>
<link rel="stylesheet" href="https://fonts.googleapis.com/css2?family=Bebas+Neue&family=Great+Vibes&family=Inter:ital,wght@1,700&display=swap">
<style>
  :root {
    --backdrop: #262626;
    --ink-light: #ffffff;
    --ink-dark: #111111;
    --space-deep: #1c1c22;
    --space-teal: #34464c;
    --space-violet: #4a3a55;
    --dust-rose: #a2624f;
    --dust-gold: #d8b34c;
    --core-glow: #e6ddd0;
  }
  html, body {
    margin: 0;
    width: 1200px;
    height: 1200px;
    overflow: hidden;
    background: var(--backdrop);
  }
  .book-cover {
    position: absolute;
    left: 219px;
    top: 29px;
    width: 761px;
    height: 1141px;
    overflow: hidden;
    background:
      radial-gradient(ellipse 55% 45% at 50% 58%, var(--core-glow) 0%, rgba(230,221,208,0.55) 45%, rgba(230,221,208,0) 100%),
      radial-gradient(ellipse 60% 50% at 100% 100%, var(--dust-gold) 0%, rgba(216,179,76,0) 100%),
      radial-gradient(ellipse 60% 55% at 0% 100%, var(--dust-rose) 0%, rgba(162,98,79,0) 100%),
      radial-gradient(ellipse 50% 45% at 0% 45%, var(--space-violet) 0%, rgba(74,58,85,0) 100%),
      radial-gradient(ellipse 55% 40% at 100% 10%, var(--space-teal) 0%, rgba(52,70,76,0) 100%),
      linear-gradient(160deg, var(--space-deep) 0%, #3a3a40 40%, #8a7a6a 75%, #b99a5a 100%);
  }
  .cosmic-field {
    position: absolute;
    inset: 0;
  }
  .geometry-art {
    position: absolute;
    left: 36px;
    top: 381px;
    width: 686px;
    height: 640px;
    border-radius: 50%;
    background: radial-gradient(circle at 50% 50%, rgba(255,255,255,0.35) 0%, rgba(255,255,255,0.12) 55%, rgba(255,255,255,0) 72%);
  }
  .series-line {
    position: absolute;
    top: 73px;
    left: 0;
    width: 100%;
    text-align: center;
    font-family: "Bebas Neue", sans-serif;
    font-size: 38px;
    letter-spacing: 0.2em;
    color: var(--ink-light);
    margin: 0;
    line-height: 1;
  }
  .series-line .series-number { font-style: italic; }
  .title-main {
    position: absolute;
    top: 118px;
    left: 0;
    width: 100%;
    text-align: center;
    font-family: "Bebas Neue", sans-serif;
    font-weight: 400;
    font-size: 190px;
    line-height: 1;
    color: var(--ink-light);
    margin: 0;
  }
  .title-script {
    position: absolute;
    top: 238px;
    left: 0;
    width: 100%;
    text-align: center;
    font-family: "Great Vibes", cursive;
    font-size: 150px;
    line-height: 1.1;
    color: var(--ink-light);
    margin: 0;
  }
  .subtitle {
    position: absolute;
    top: 640px;
    left: 0;
    width: 100%;
    text-align: center;
    font-family: "Inter", sans-serif;
    font-style: italic;
    font-weight: 700;
    font-size: 30px;
    line-height: 1.25;
    letter-spacing: -0.01em;
    color: var(--ink-dark);
    margin: 0;
  }
  .author {
    position: absolute;
    top: 1063px;
    left: 0;
    width: 100%;
    text-align: center;
    font-family: "Bebas Neue", sans-serif;
    font-size: 40px;
    letter-spacing: 0.3em;
    color: var(--ink-dark);
    margin: 0;
    line-height: 1;
  }
</style>
</head>
<body>
  <main class="book-cover">
    <div class="cosmic-field" role="img" aria-label="Starry nebula background with light rays"></div>
    <div class="geometry-art" role="img" aria-label="Glowing sacred geometry star pattern"></div>
    <p class="series-line">Venture <span class="series-number">482</span> Ascended</p>
    <h1 class="title-main">Shaping</h1>
    <p class="title-script">Outcomes</p>
    <p class="subtitle">Paths To Unlocking<br>Cosmic Truths</p>
    <p class="author">Dorian Pell</p>
  </main>
</body>
</html>
```